Design NEW business card

We would like a business card using the colour deep red wine or dark navy blue textured background (patterned or not, open to suggestions) with a high gloss debossed rose gold/copper RM Roland Mercer Jewellery business name (Provided). I have included images for your review we would like to keep our currently logo and business name on the front but you can change the layout and positioning. For the back of the card we are open to all suggestions/variations.
Business
Use our current RM Roland Mercer Jewellery logo (Provided image)

```html
<!DOCTYPE html>
<html lang="en">
<head>
<meta charset="utf-8">
<title>Roland Mercer Jewellery – Business Card</title>
<link rel="stylesheet" href="https://fonts.googleapis.com/css2?family=Montserrat:wght@300;400&family=Roboto:wght@400&display=swap">
<style>
  :root {
    --backdrop: #a9a9a9;
    --paper: #f4f4f2;
    --wine: #5a2129;
    --rose-light: #e2b594;
    --rose-mid: #c4926f;
    --rose-dark: #a06f4d;
    --rose-text: #b8866a;
    --rose-text-soft: #c99c7e;
    --ink-grey: #444;
    --white: #ffffff;
  }
  * { margin: 0; padding: 0; box-sizing: border-box; }
  html, body { width: 1200px; height: 960px; overflow: hidden; }
  body {
    background: var(--backdrop);
    font-family: "Montserrat", sans-serif;
    position: relative;
  }
  .card {
    position: absolute;
    left: 320px;
    width: 602px;
    height: 342px;
    overflow: hidden;
    box-shadow: 0 3px 8px rgba(0,0,0,.25);
  }
  .card-front { top: 102px; background: var(--paper); }
  .card-back { top: 493px; background: var(--wine); }

  .brand-name {
    position: absolute;
    font-family: "Montserrat", sans-serif;
    font-weight: 300;
    text-transform: uppercase;
    line-height: 1;
  }
  .brand-name .line { display: block; }
  .card-front .brand-name {
    left: 0; right: 0; top: 198px;
    text-align: center;
    color: var(--rose-text);
  }
  .card-front .brand-name .primary { font-size: 23px; letter-spacing: 4px; padding-left: 110px; }
  .card-front .brand-name .secondary { font-size: 9px; letter-spacing: 13px; margin-top: 8px; padding-left: 110px; }

  .website-front {
    position: absolute;
    left: 0; right: 0; top: 300px;
    text-align: center;
    font-family: "Roboto", sans-serif;
    font-size: 14px;
    letter-spacing: 5px;
    color: var(--ink-grey);
  }

  .back-art { position: absolute; inset: 0; }
  .card-back .brand-name {
    left: 88px; top: 132px;
    color: var(--rose-text-soft);
  }
  .card-back .brand-name .primary { font-size: 17px; letter-spacing: 3px; }
  .card-back .brand-name .secondary { font-size: 7px; letter-spacing: 10px; margin-top: 7px; }

  .contact {
    position: absolute;
    right: 38px;
    text-align: right;
    color: var(--white);
    font-family: "Montserrat", sans-serif;
    font-weight: 400;
  }
  .person { top: 38px; }
  .person-name { font-size: 19px; font-weight: 300; letter-spacing: .3px; }
  .person-role { font-size: 12px; margin-top: 4px; }
  .address { top: 165px; font-size: 13.5px; line-height: 19px; }
  .lines { top: 211px; right: 38px; font-size: 13.5px; line-height: 19.3px; }
  .lines li { list-style: none; display: flex; justify-content: flex-end; align-items: center; gap: 6px; }
  .lines svg { width: 12px; height: 12px; fill: var(--white); flex: none; }
</style>
</head>
<body>

<section class="card card-front">
  <div class="brand-name">
    <span class="line primary">Roland Mercer</span>
    <span class="line secondary">Jewellery</span>
  </div>
  <p class="website-front">www.rmjewellery.com</p>
</section>

<section class="card card-back">
  <svg class="back-art" viewBox="0 0 602 342" preserveAspectRatio="none" aria-hidden="true">
    <defs>
      <radialGradient id="roseGlow" cx="62%" cy="52%" r="60%">
        <stop offset="0" stop-color="var(--rose-light)"/>
        <stop offset=".55" stop-color="var(--rose-mid)"/>
        <stop offset="1" stop-color="var(--rose-dark)"/>
      </radialGradient>
    </defs>
    <path d="M372,0 L602,0 L602,342 L130,342 C270,260 385,150 372,0 Z" fill="url(#roseGlow)"/>
    <path d="M395,20 C410,150 330,270 150,342 L168,342 C345,270 418,150 395,20 Z" fill="var(--wine)"/>
  </svg>

  <div class="brand-name">
    <span class="line primary">Roland Mercer</span>
    <span class="line secondary">Jewellery</span>
  </div>

  <div class="contact person">
    <p class="person-name">ADELE HARTWELL</p>
    <p class="person-role">CEO/FOUNDER</p>
  </div>

  <div class="contact address">
    <p>214 Birchwood Row</p>
    <p>Fairmont, Oregon 97310</p>
  </div>

  <ul class="contact lines">
    <li>541 208 7736
      <svg viewBox="0 0 24 24"><path d="M6.6 10.8a15 15 0 0 0 6.6 6.6l2.2-2.2c.3-.3.7-.4 1-.2 1.1.4 2.3.6 3.6.6.6 0 1 .4 1 1V20c0 .6-.4 1-1 1C10.6 21 3 13.4 3 4c0-.6.4-1 1-1h3.5c.6 0 1 .4 1 1 0 1.3.2 2.5.6 3.6.1.3 0 .7-.2 1z"/></svg>
    </li>
    <li>541 390 1182
      <svg viewBox="0 0 24 24"><path d="M7 1h10a2 2 0 0 1 2 2v18a2 2 0 0 1-2 2H7a2 2 0 0 1-2-2V3a2 2 0 0 1 2-2zm0 3v14h10V4z"/></svg>
    </li>
    <li>541 208 7740
      <svg viewBox="0 0 24 24"><path d="M6 2h10l2 2v5H6zM3 10h18a1 1 0 0 1 1 1v8a1 1 0 0 1-1 1H3a1 1 0 0 1-1-1v-8a1 1 0 0 1 1-1zm3 4v2h5v-2z"/></svg>
    </li>
    <li>hello@rmjewellery.com
      <svg viewBox="0 0 24 24"><path d="M2 5h20v14H2zm2 2v.5l8 5 8-5V7l-8 5z"/></svg>
    </li>
    <li>www.rmjewellery.com
      <svg viewBox="0 0 24 24"><path d="M12 2a10 10 0 1 0 0 20 10 10 0 0 0 0-20zm-1 17.9A8 8 0 0 1 4.2 10L9 15v1a2 2 0 0 0 2 2zm6.9-2.5A2 2 0 0 0 16 16h-1v-3a1 1 0 0 0-1-1H8v-2h2a1 1 0 0 0 1-1V7h2a2 2 0 0 0 2-2v-.4a8 8 0 0 1 2.9 12.8z"/></svg>
    </li>
  </ul>
</section>

</body>
</html>
```